Fresh, modern, fun business card for pediatric dental practice

Need a business card for fresh, modern, fun pediatric dental practice

Clean look that matches our website's font and colors

We prefer the look of curved corners on business cards

Target Market(s)

parents (mothers) of young children, professionals, mid-high class

Industry/Entity Type

Dental

Contact Information for Business Card

Maplebrook Pediatric Dentistry
482 Quarry Lane
Suite 517
Fernvale, PA 17590
717.555.0193
www.maplebrookkidsdental.example

Mei-Ran Tsai, DMD
Corinne Walbeck, DMD
(we are working on our email address, but we would like that on the card as well)

Font styles to use
Sans Serif

Requirements
Must have
• All info; we would also like to make cards for individual staff members
• colors from our website and color palatte, attatched
• use same font and design as website for branding
Nice to have
• clean, simple card that has a pop of color
• we would like to see a few designs with our tag line "where every grin grows bold"
• we are not sure if we want to have it on there or not
• we would like to see a few designs incorporating the ribbon graphic on our website where the word WELCOME is

```html
<!DOCTYPE html>
<html lang="en">
<head>
<meta charset="utf-8">
<title>Maplebrook Pediatric Dentistry – Business Card</title>
<link href="https://fonts.googleapis.com/css2?family=Lato:wght@400;700&family=Roboto:wght@500;700&display=swap" rel="stylesheet">
<style>
  :root {
    --magenta: #c0287f;
    --magenta-light: #d9399f;
    --sun: #e9a620;
    --ink: #3a3a3a;
    --paper: #ffffff;
    --paper-shade: #e6e6e6;
    --backdrop: #9c9c9c;
  }
  * { box-sizing: border-box; margin: 0; padding: 0; }
  html, body { width: 1200px; height: 900px; overflow: hidden; }
  body {
    background: var(--backdrop);
    font-family: "Lato", sans-serif;
    position: relative;
  }
  .card {
    position: absolute;
    left: 285px;
    width: 630px;
    height: 360px;
    border-radius: 22px;
    overflow: hidden;
    box-shadow: 0 6px 18px rgba(0,0,0,0.25);
  }
  /* front */
  .card-front {
    top: 50px;
    background: linear-gradient(135deg, var(--magenta) 0%, var(--magenta-light) 100%);
    display: flex;
    align-items: center;
    justify-content: center;
    gap: 14px;
  }
  .brand-dot {
    width: 26px; height: 26px; border-radius: 50%;
    flex: none;
  }
  .card-front .brand-dot { background: #ffffff; }
  .card-front .brand-name {
    color: #ffffff;
    font-weight: 700;
    font-size: 30px;
    letter-spacing: 0.5px;
  }
  /* back */
  .card-back {
    top: 470px;
    background: linear-gradient(180deg, var(--paper) 40%, var(--paper-shade) 100%);
  }
  .back-brand {
    position: absolute;
    left: 30px; top: 0;
    width: 250px; height: 262px;
    display: flex; align-items: center; justify-content: center; gap: 10px;
  }
  .back-brand .brand-dot { background: var(--sun); width: 20px; height: 20px; }
  .back-brand .brand-name {
    color: var(--sun);
    font-weight: 700;
    font-size: 23px;
    line-height: 1.15;
  }
  .divider {
    position: absolute;
    left: 300px; top: 40px;
    width: 2px; height: 182px;
    background: var(--sun);
  }
  .details {
    position: absolute;
    left: 322px; top: 32px;
    right: 16px;
    color: var(--ink);
  }
  .doctor {
    font-family: "Roboto", sans-serif;
    font-weight: 700;
    font-size: 21px;
    color: var(--magenta);
    line-height: 1.3;
    white-space: nowrap;
  }
  .doctor .degree { color: var(--sun); font-weight: 500; }
  .address {
    margin-top: 10px;
    font-size: 13.5px;
    line-height: 1.35;
  }
  .contact-list { list-style: none; margin-top: 12px; }
  .contact-list li {
    display: flex; align-items: center; gap: 8px;
    font-size: 13.5px; line-height: 1; margin-bottom: 6px;
    white-space: nowrap;
  }
  .contact-icon {
    width: 17px; height: 17px; border-radius: 50%;
    background: var(--magenta);
    display: flex; align-items: center; justify-content: center;
    flex: none;
  }
  .tagline-band {
    position: absolute;
    left: 0; right: 0; bottom: 22px;
    height: 76px;
    background: var(--magenta);
    display: flex; align-items: center; justify-content: center;
  }
  .tagline {
    color: #ffffff;
    font-size: 17px;
    letter-spacing: 0.3px;
    margin-left: 60px;
  }
</style>
</head>
<body>

<section class="card card-front">
  <span class="brand-dot"></span>
  <span class="brand-name">Maplebrook Pediatric Dentistry</span>
</section>

<section class="card card-back">
  <div class="back-brand">
    <span class="brand-dot"></span>
    <span class="brand-name">Maplebrook<br>Pediatric Dentistry</span>
  </div>

  <div class="divider"></div>

  <div class="details">
    <p class="doctor">Mei-Ran Tsai, <span class="degree">DMD</span></p>
    <p class="doctor">Corinne Walbeck, <span class="degree">DMD</span></p>
    <p class="address">482 Quarry Lane, Suite 517<br>Fernvale, PA 17590</p>
    <ul class="contact-list">
      <li>
        <span class="contact-icon">
          <svg width="10" height="10" viewBox="0 0 24 24"><path fill="#fff" d="M6.6 10.8a15 15 0 0 0 6.6 6.6l2.2-2.2a1 1 0 0 1 1-.25 11.4 11.4 0 0 0 3.6.57 1 1 0 0 1 1 1V20a1 1 0 0 1-1 1A17 17 0 0 1 3 4a1 1 0 0 1 1-1h3.5a1 1 0 0 1 1 1c0 1.25.2 2.45.57 3.57a1 1 0 0 1-.25 1z"/></svg>
        </span>717.555.0193
      </li>
      <li>
        <span class="contact-icon">
          <svg width="10" height="10" viewBox="0 0 24 24"><rect x="2" y="5" width="20" height="14" rx="2" fill="#fff"/><path d="M3 6l9 7 9-7" fill="none" stroke="#c0287f" stroke-width="2"/></svg>
        </span>info@maplebrookkidsdental.example
      </li>
      <li>
        <span class="contact-icon">
          <svg width="10" height="10" viewBox="0 0 24 24"><circle cx="12" cy="12" r="9" fill="none" stroke="#fff" stroke-width="2.5"/><path d="M3 12h18M12 3c3 3 3 15 0 18M12 3c-3 3-3 15 0 18" fill="none" stroke="#fff" stroke-width="2"/></svg>
        </span>www.maplebrookkidsdental.example
      </li>
    </ul>
  </div>

  <div class="tagline-band">
    <p class="tagline">where every grin grows bold</p>
  </div>
</section>

</body>
</html>
```